Tour Guide in Israel business card

I am a tour guide in Israel (the holy land). Prior to it I have over 20 years high-tech business. My main (but not only) focus is working with business people that come to Israel and want to get a tour (usually short from few hours to 2 days). During my guiding I incorporate a lot of my know how of the Israeli business culture. I like to have a business card that I can present to anyone that is looking for a tour guide, but that business people will understand the additional value I can provide them during my tour.

Target Market(s)

Business visitors and tourist to Israel

Industry/Entity Type

Tourism

Contact Information for Business Card

Danny Korvath
email: danny@korvath-tours.example
Mobile: +972-52-7416205

Colors

Designer to choose colors to be used in the design.

Requirements
Must have
• Tour Guide
Nice to have
• I don't know how but it should project my understanding in business not just the tourist side of my knowledge.

```html
<!DOCTYPE html>
<html lang="en">
<head>
<meta charset="utf-8">
<title>Danny Korvath – Tour Leader &amp; Storyteller business card</title>
<link rel="stylesheet" href="https://fonts.googleapis.com/css2?family=Arimo:wght@400;700&display=swap">
<style>
  :root {
    --backdrop: #2b2b2d;
    --card-white: #f4f4f4;
    --card-white-shade: #e2e2e2;
    --navy: #0f3550;
    --navy-name: #1d4a6b;
    --ink-grey: #555a5e;
    --deep-blue-top: #1d6a93;
    --deep-blue-bottom: #031726;
    --glow-cyan: #3fc3f2;
    --glow-soft: #7fdcff;
  }
  * { box-sizing: border-box; margin: 0; padding: 0; }
  html, body {
    width: 1200px; height: 890px; overflow: hidden;
    background: var(--backdrop);
    font-family: "Arimo", Arial, sans-serif;
  }
  .canvas {
    position: relative; width: 1200px; height: 890px;
    display: flex; justify-content: center; align-items: center; gap: 110px;
  }
  .card {
    position: relative; width: 340px; height: 595px;
    box-shadow: 0 14px 30px rgba(0,0,0,.45);
  }

  /* Contact side */
  .card--contact {
    background: linear-gradient(160deg, var(--card-white) 0%, var(--card-white-shade) 100%);
  }
  .contact__name {
    position: absolute; left: 46px; top: 205px;
    line-height: 1;
  }
  .contact__first {
    display: block; font-size: 36px; font-weight: 400;
    color: var(--navy-name); letter-spacing: .5px;
  }
  .contact__last {
    display: block; font-size: 36px; font-weight: 700;
    color: var(--navy); letter-spacing: .5px; margin-top: 2px;
  }
  .contact__role {
    position: absolute; left: 40px; top: 292px;
    font-size: 19px; color: var(--ink-grey);
  }
  .contact__details {
    position: absolute; left: 30px; top: 370px;
    list-style: none; font-size: 19px; color: var(--ink-grey);
    line-height: 33px;
  }

  /* Tagline side */
  .card--tagline {
    background: linear-gradient(175deg, var(--deep-blue-top) 0%, #0b3d5e 45%, var(--deep-blue-bottom) 100%);
    color: var(--glow-cyan);
  }
  .network-map {
    position: absolute; left: 118px; top: 95px; width: 118px; height: 330px;
    border-radius: 40px 60px 30px 30px;
    background: radial-gradient(ellipse at 50% 45%, rgba(127,220,255,.45) 0%, rgba(63,195,242,.18) 55%, rgba(63,195,242,0) 80%);
  }
  .theme-word {
    position: absolute; font-size: 19px; color: var(--glow-cyan);
    white-space: nowrap;
  }
  .theme-word--land { left: 180px; top: 64px; }
  .theme-word--people { left: 48px; top: 150px; transform: rotate(-35deg); }
  .theme-word--history { left: 238px; top: 200px; transform: rotate(80deg); transform-origin: left top; }
  .theme-word--culture { left: 40px; top: 285px; transform: rotate(-80deg); }
  .theme-word--business { left: 236px; top: 285px; transform: rotate(80deg); transform-origin: left top; }
  .theme-word--faith { left: 50px; top: 395px; transform: rotate(-80deg); }
  .tagline {
    position: absolute; left: 0; right: 0; bottom: 70px;
    text-align: center; font-size: 22px; letter-spacing: 2px;
    color: var(--glow-cyan);
  }
</style>
</head>
<body>
  <main class="canvas">
    <section class="card card--contact" aria-label="Contact side">
      <h1 class="contact__name">
        <span class="contact__first">DANNY</span>
        <span class="contact__last">KORVATH</span>
      </h1>
      <p class="contact__role">Tour Leader &amp; Storyteller</p>
      <ul class="contact__details">
        <li>+972-52-7416205</li>
        <li>danny@korvath-tours.example</li>
        <li>www.korvath-tours.example</li>
      </ul>
    </section>

    <section class="card card--tagline" aria-label="Tagline side">
      <div class="network-map" role="img" aria-label="Glowing map of Israel drawn as a network of connected dots"></div>
      <span class="theme-word theme-word--land">Land</span>
      <span class="theme-word theme-word--people">People</span>
      <span class="theme-word theme-word--history">History</span>
      <span class="theme-word theme-word--culture">Culture</span>
      <span class="theme-word theme-word--business">Business</span>
      <span class="theme-word theme-word--faith">Faith</span>
      <p class="tagline">CONNECTING THE DOTS</p>
    </section>
  </main>
</body>
</html>
```